Business Card design for law firm = Brightvale Australia

We are seeking a new design for our business cards.
We are keeping our logo, which is attached.
We need space for
Name
Title
Address is , which is
Level 7
214 Marlowe Street
Sydney NSW 2047
Phone :
Mobile :
Fax :
Email :
DX :
website www.brightvale-example.com.au

Industry/Entity Type

Law Firm / Banking and Finance

Contact Information for Business Card

We are seeking a new design for our business cards. We are keeping our logo. We need space for Name Title Address is Level 7 214 Marlowe Street Sydney NSW 2047 Phone Mobile Fax Email DX website www.brightvale-example.com.au

Colors
0054AA
0677BA
7BADD7
CADEEF
E8F1F8

Requirements
Must have
• see our website for general feel www.brightvale-example.com.au

```html
<!DOCTYPE html>
<html lang="en">
<head>
<meta charset="utf-8">
<title>Brightvale Australia – Business Card</title>
<link rel="stylesheet" href="https://fonts.googleapis.com/css2?family=EB+Garamond:ital,wght@0,400;1,400&display=swap">
<style>
  :root {
    --backdrop: #2b2b2b;
    --card: #ededed;
    --navy: #2a4a9c;
    --cyan: #1191c8;
    --ink: #2a2a2a;
  }
  * { margin: 0; padding: 0; box-sizing: border-box; }
  html, body { width: 1200px; height: 1138px; overflow: hidden; }
  body {
    background: var(--backdrop);
    position: relative;
    font-family: "EB Garamond", Georgia, serif;
    color: var(--ink);
  }
  .card {
    position: absolute;
    background: var(--card);
    border-radius: 18px;
    overflow: hidden;
  }
  .card--front { left: 272px; top: 184px; width: 622px; height: 376px; }
  .card--back  { left: 274px; top: 606px; width: 619px; height: 375px; }

  .brand-name {
    position: absolute;
    font-weight: 400;
    color: var(--navy);
    line-height: 1;
    white-space: nowrap;
  }

  /* Front */
  .card--front .brand-name { left: 0; width: 100%; text-align: center; top: 146px; font-size: 54px; }
  .front-web {
    position: absolute; left: 0; width: 100%; top: 334px;
    text-align: center; font-size: 15px; letter-spacing: 0.45em;
  }
  .front-bar {
    position: absolute; left: 142px; bottom: 0; width: 340px; height: 9px;
    background: var(--navy);
  }

  /* Back */
  .person-name {
    position: absolute; left: 32px; top: 36px;
    font-size: 29px; color: var(--navy); line-height: 1;
  }
  .person-rule {
    position: absolute; left: 20px; top: 74px; width: 155px; height: 2px;
    background: var(--navy); border-radius: 2px;
  }
  .person-title {
    position: absolute; left: 32px; top: 80px;
    font-size: 16px; font-style: italic;
  }
  .address {
    position: absolute; left: 33px; top: 208px;
    font-size: 16px; line-height: 20px;
  }
  .contact-list {
    position: absolute; left: 30px; top: 259px; list-style: none;
    font-size: 16px; line-height: 20px;
  }
  .contact-list li { display: flex; align-items: center; gap: 19px; }
  .contact-list svg { width: 12px; height: 12px; fill: var(--cyan); flex: none; }
  .card--back .brand-name { right: 30px; top: 252px; font-size: 42px; }
</style>
</head>
<body>
  <section class="card card--front">
    <div class="brand-name">Brightvale</div>
    <div class="front-web">www.brightvale-example.com.au</div>
    <div class="front-bar"></div>
  </section>

  <section class="card card--back">
    <div class="person-name">Sam Carrow</div>
    <div class="person-rule"></div>
    <div class="person-title">Managing Director</div>

    <div class="address">Level 7 214 Marlowe Street<br>Sydney NSW 2047</div>

    <ul class="contact-list">
      <li>
        <svg viewBox="0 0 12 12" aria-hidden="true"><path d="M1 4c0-2 2-3 5-3s5 1 5 3v1H8.5V3.5h-5V5H1zM3 6h6l1.5 5h-9z"/></svg>
        <span>02 9000 0122</span>
      </li>
      <li>
        <svg viewBox="0 0 12 12" aria-hidden="true"><path d="M3 1h6v3H3zM1 4.5h10v5H9V8H3v1.5H1zM3.5 8.5h5V11h-5z"/></svg>
        <span>02 9000 6411</span>
      </li>
      <li>
        <svg viewBox="0 0 12 12" aria-hidden="true"><path d="M0.5 2.5h11v7h-11zM1.5 3.5l4.5 3.5 4.5-3.5v-0.2h-9z" fill-rule="evenodd"/></svg>
        <span>sam.carrow@brightvale-example.com.au</span>
      </li>
      <li>
        <svg viewBox="0 0 12 12" aria-hidden="true"><path d="M6 0.5a5.5 5.5 0 1 0 0 11a5.5 5.5 0 1 0 0-11zM2 5.5h8v1H2zM5.5 1.5h1v9h-1z"/></svg>
        <span>www.brightvale-example.com.au</span>
      </li>
    </ul>

    <div class="brand-name">Brightvale</div>
  </section>
</body>
</html>
```